Oil and Gas Exploration and Production company needs a business card design

We need a business card design using our logo and colors in the logo. We want a mainstream design.

```html
<!DOCTYPE html>
<html lang="en">
<head>
<meta charset="utf-8">
<title>Sunvale Oil &amp; Gas – Business Card</title>
<link href="https://fonts.googleapis.com/css2?family=Roboto+Slab:wght@300;400;700;800&family=Roboto:wght@400&display=swap" rel="stylesheet">
<style>
  :root {
    --backdrop: #6e4c36;
    --card-white: #f4f4f2;
    --ink: #231f20;
    --gold: #c8972e;
    --muted: #3a3a3a;
    --white: #ffffff;
  }
  * { margin: 0; padding: 0; box-sizing: border-box; }
  html, body { width: 1200px; height: 960px; overflow: hidden; }
  body { background: var(--backdrop); position: relative; font-family: "Roboto Slab", serif; }

  .card { position: absolute; width: 600px; height: 343px; box-shadow: 0 3px 6px rgba(0,0,0,0.45); }
  .card-front { left: 315px; top: 113px; background: var(--card-white); }
  .card-back { left: 311px; top: 472px; background: var(--gold); }

  .emblem-circle { position: absolute; left: 27px; top: 104px; width: 224px; height: 224px; border-radius: 50%; background: var(--ink); }

  .holder { position: absolute; right: 38px; top: 46px; text-align: right; }
  .holder-name { font-weight: 800; font-size: 22px; letter-spacing: 0.5px; color: var(--ink); line-height: 1; }
  .holder-title { font-weight: 400; font-size: 14px; color: var(--gold); margin-top: 3px; letter-spacing: 0.3px; }

  .address { position: absolute; right: 38px; top: 165px; text-align: right; font-weight: 300; font-size: 13px; line-height: 18px; color: var(--muted); }

  .contact-list { position: absolute; right: 40px; top: 213px; list-style: none; text-align: right; font-weight: 300; font-size: 13px; color: var(--muted); }
  .contact-list li { height: 19px; line-height: 19px; display: flex; justify-content: flex-end; align-items: center; gap: 6px; }
  .contact-list svg { width: 13px; height: 13px; fill: var(--ink); }

  .wordmark { position: absolute; left: 160px; top: 105px; display: flex; align-items: center; gap: 14px; }
  .wordmark-dot { width: 40px; height: 40px; border-radius: 50%; background: var(--ink); flex: none; }
  .wordmark-text { font-weight: 800; color: var(--ink); line-height: 1; }
  .wordmark-name { font-size: 64px; letter-spacing: -1px; }
  .wordmark-sector { font-size: 26px; letter-spacing: 3px; margin-top: 6px; text-align: right; }

  .back-web { position: absolute; left: 0; right: 0; top: 288px; text-align: center; font-family: "Roboto", sans-serif; font-size: 14px; letter-spacing: 4.5px; color: var(--white); }
</style>
</head>
<body>
  <section class="card card-front">
    <div class="emblem-circle"></div>

    <div class="holder">
      <p class="holder-name">MARA DALTON</p>
      <p class="holder-title">CEO/FOUNDER</p>
    </div>

    <p class="address">412 Birchwood Road<br>Fairbanks, Alaska 99701</p>

    <ul class="contact-list">
      <li>555 210 4481
        <svg viewBox="0 0 16 16" aria-hidden="true"><path d="M3 1l3 3-1.5 2a9 9 0 0 0 5.5 5.5L12 10l3 3-2 2C7 15 1 9 1 3z"/></svg></li>
      <li>555 372 9016
        <svg viewBox="0 0 16 16" aria-hidden="true"><path d="M4 0h8v16H4zM5.5 2v10h5V2zM7 13.5h2v1H7z" fill-rule="evenodd"/></svg></li>
      <li>555 648 2273
        <svg viewBox="0 0 16 16" aria-hidden="true"><path d="M4 1h8v4H4zM1 6h14v6h-3v3H4v-3H1zM5.5 10v3.5h5V10z" fill-rule="evenodd"/></svg></li>
      <li>info@sunvaleoil.com
        <svg viewBox="0 0 16 16" aria-hidden="true"><path d="M1 3h14v10H1zM2.5 4.5L8 9l5.5-4.5v7h-11z" fill-rule="evenodd"/></svg></li>
      <li>www.sunvaleoil.com
        <svg viewBox="0 0 16 16" aria-hidden="true"><circle cx="8" cy="8" r="7"/></svg></li>
    </ul>
  </section>

  <section class="card card-back">
    <div class="wordmark">
      <span class="wordmark-dot"></span>
      <div class="wordmark-text">
        <p class="wordmark-name">Sunvale</p>
        <p class="wordmark-sector">OIL &amp; GAS</p>
      </div>
    </div>
    <p class="back-web">www.sunvaleoil.com</p>
  </section>
</body>
</html>
```